Business card for Sports Apparel business

DOUBLE SIDED DESIGN
We need business cards for a new sports apparel business. We are developing a protective headband for soccer initially.
Torvalle is focused on designing and developing head protection products to reduce the likelihood of concussion when playing sports. Exploring and understanding medical insights, material science research, current and former players experiences and governing bodies guidelines has allowed Torvalle to develop the safety, style, form and function requirements of a suitable product to bring to market.
Target Market(s)
Mums buying kits for the sons and daughters. Amateur footballers.
Industry/Entity Type
Sporting Good
Contact Information for Business Card
Martin Ashworth - CEO
Mobile: +44 7431589027
Email: martin@torvalle.co.uk
Tel: 0208 5519372
Helena Pargeter - COO
Mob: +44 7385 640117
Email: helena@torvalle.co.uk
Tel: 0208 5519372
Duncan Farrow - CCO
Mob: +44 7564 293081
Email: duncan@torvalle.co.uk
Tel: 0208 5519372
Look and feel
Each slider illustrates characteristics of the customer's brand and the style your logo design should communicate.

```html
<!DOCTYPE html>
<html lang="en">
<head>
<meta charset="utf-8">
<title>Torvalle business card</title>
<link rel="stylesheet" href="https://fonts.googleapis.com/css2?family=Montserrat:wght@400;500;700&display=swap">
<style>
  :root {
    --canvas: #e9eaec;
    --card-dark: #1b1b1b;
    --pitch-mid: #2e2e2e;
    --pitch-edge: #121212;
    --brand-blue: #0f5e9c;
    --ink: #2b2b2b;
    --muted: #4a4a4a;
    --paper: #ffffff;
    --divider: #c9d6e2;
  }
  * { box-sizing: border-box; margin: 0; padding: 0; }
  html, body { width: 1200px; height: 1015px; overflow: hidden; }
  body {
    background: var(--canvas);
    font-family: "Montserrat", sans-serif;
    display: flex;
    flex-direction: column;
    align-items: center;
    justify-content: center;
    gap: 24px;
  }
  .card {
    position: relative;
    width: 840px;
    height: 480px;
    overflow: hidden;
    box-shadow: 0 6px 18px rgba(0,0,0,0.18);
  }
  .card::after {
    content: "";
    position: absolute;
    left: 0; right: 0; bottom: 0;
    height: 16px;
    background: var(--brand-blue);
  }
  /* Front */
  .card-front { background: var(--card-dark); }
  .pitch-photo {
    position: absolute;
    inset: 0;
    background: radial-gradient(ellipse at 50% 45%, var(--pitch-mid) 0%, var(--card-dark) 60%, var(--pitch-edge) 100%);
  }
  .front-brand {
    position: absolute;
    inset: 0 0 16px 0;
    display: flex;
    align-items: center;
    justify-content: center;
    gap: 18px;
  }
  .brand-square {
    width: 26px; height: 26px;
    background: var(--paper);
  }
  .front-brand .brand-name {
    color: var(--paper);
    font-weight: 500;
    font-size: 64px;
    letter-spacing: 2px;
  }
  /* Back */
  .card-back { background: var(--paper); }
  .back-brand {
    position: absolute;
    left: 70px;
    top: 200px;
    display: flex;
    align-items: center;
    gap: 12px;
  }
  .back-brand .brand-square { width: 18px; height: 18px; background: var(--brand-blue); }
  .back-brand .brand-name {
    color: var(--brand-blue);
    font-weight: 500;
    font-size: 42px;
    letter-spacing: 1px;
  }
  .divider {
    position: absolute;
    left: 440px;
    top: 92px;
    width: 1px;
    height: 180px;
    background: var(--divider);
  }
  .contact {
    position: absolute;
    left: 474px;
    top: 96px;
  }
  .person-name {
    color: var(--brand-blue);
    font-weight: 700;
    font-size: 26px;
    letter-spacing: 0.3px;
  }
  .person-role {
    color: var(--ink);
    font-size: 18px;
    margin: 2px 0 18px;
  }
  .contact-list { list-style: none; }
  .contact-list li {
    display: flex;
    align-items: center;
    gap: 12px;
    color: var(--ink);
    font-size: 18px;
    line-height: 30px;
  }
  .contact-list svg { width: 22px; height: 22px; flex: none; }
</style>
</head>
<body>
  <section class="card card-front">
    <div class="pitch-photo" role="img" aria-label="Dark overhead photograph of a football pitch with faint white line markings"></div>
    <div class="front-brand">
      <span class="brand-square"></span>
      <span class="brand-name">TORVALLE</span>
    </div>
  </section>

  <section class="card card-back">
    <div class="back-brand">
      <span class="brand-square"></span>
      <span class="brand-name">TORVALLE</span>
    </div>
    <div class="divider"></div>
    <div class="contact">
      <p class="person-name">MARTIN ASHWORTH</p>
      <p class="person-role">CEO</p>
      <ul class="contact-list">
        <li>
          <svg viewBox="0 0 22 22" aria-hidden="true"><rect x="1" y="1" width="20" height="20" rx="3" fill="none" stroke="#0f5e9c" stroke-width="2"/><path d="M7 5l2.5 0 1 3-1.5 1.2a7 7 0 0 0 3.3 3.3L13.5 11l3 1v2.5c0 .8-.7 1.5-1.5 1.5A10 10 0 0 1 6 7 1.5 1.5 0 0 1 7 5z" fill="#0f5e9c"/></svg>
          0208 5519372
        </li>
        <li>
          <svg viewBox="0 0 22 22" aria-hidden="true"><rect x="1" y="1" width="20" height="20" rx="3" fill="none" stroke="#0f5e9c" stroke-width="2"/><rect x="7" y="4.5" width="8" height="13" rx="1.5" fill="none" stroke="#0f5e9c" stroke-width="1.6"/><circle cx="11" cy="15" r="0.9" fill="#0f5e9c"/></svg>
          +44 7431589027
        </li>
        <li>
          <svg viewBox="0 0 22 22" aria-hidden="true"><rect x="1" y="1" width="20" height="20" rx="3" fill="#0f5e9c"/><rect x="5" y="7" width="12" height="8" fill="none" stroke="#fff" stroke-width="1.5"/><path d="M5 7l6 5 6-5" fill="none" stroke="#fff" stroke-width="1.5"/></svg>
          martin@torvalle.co.uk
        </li>
      </ul>
    </div>
  </section>
</body>
</html>
```